MRT Property - Business Cards

Looking for a business card & general letterhead, signage etc design for our new logo.

Colours:
000a20
0056a2
00b5ef
0088ce
68cef2

Fonts:
Poppins
Karla

Please keep look and feel of new brand - example in the zip package I sent.

```html
<!DOCTYPE html>
<html lang="en">
<head>
<meta charset="utf-8">
<title>MRT Property – Stationery</title>
<link href="https://fonts.googleapis.com/css2?family=Poppins:wght@400;600&display=swap" rel="stylesheet">
<style>
  :root {
    --ink: #000a20;
    --navy: #0056a2;
    --deep-blue: #0d4fa0;
    --mid-blue: #0088ce;
    --sky: #68cef2;
    --envelope: #5dbde1;
    --envelope-edge: #4aa9cf;
    --paper: #ffffff;
    --slip-paper: #f4f5f6;
    --backdrop: #d9d9d9;
  }
  * { margin: 0; padding: 0; box-sizing: border-box; }
  html, body { width: 1200px; height: 686px; overflow: hidden; }
  body {
    background: var(--backdrop);
    font-family: "Poppins", sans-serif;
    color: var(--ink);
    position: relative;
  }
  .sheet {
    position: absolute;
    overflow: hidden;
    box-shadow: 0 4px 14px rgba(0,0,0,0.18);
  }
  .letterhead { left: 50px; top: 33px; width: 438px; height: 620px; background: var(--paper); }
  .compliment-slip { left: 560px; top: 40px; width: 580px; height: 274px; background: var(--slip-paper); }
  .envelope { left: 560px; top: 350px; width: 580px; height: 290px; background: var(--envelope); }

  .brand-name {
    position: absolute;
    font-family: "Poppins", sans-serif;
    font-weight: 600;
    color: var(--navy);
    white-space: nowrap;
    display: flex;
    align-items: center;
    gap: 8px;
  }
  .brand-dot { display: inline-block; border-radius: 50%; background: var(--mid-blue); }
  .letterhead .brand-name { left: 40px; top: 38px; font-size: 26px; }
  .letterhead .brand-dot { width: 12px; height: 12px; }
  .compliment-slip .brand-name { right: 34px; top: 30px; font-size: 24px; }
  .compliment-slip .brand-dot { width: 11px; height: 11px; }

  .contact {
    position: absolute;
    right: 30px;
    text-align: right;
    font-size: 9px;
    line-height: 1.45;
    color: var(--ink);
  }
  .letterhead .contact { top: 104px; }
  .compliment-slip .contact { top: 80px; font-size: 8.5px; }
  .contact .address { margin-bottom: 3px; }
  .contact-line { display: flex; justify-content: flex-end; align-items: center; gap: 5px; }
  .contact-icon { width: 9px; height: 9px; flex: none; }

  .bottom-wave { position: absolute; left: 0; bottom: 0; width: 100%; }
  .letterhead .bottom-wave { height: 170px; }
  .compliment-slip .bottom-wave { height: 110px; }

  .envelope-flap { position: absolute; inset: 0; width: 100%; height: 100%; }
</style>
</head>
<body>

<section class="sheet letterhead" aria-label="Letterhead">
  <div class="brand-name"><span class="brand-dot"></span>MRT Property</div>
  <div class="contact">
    <p class="address">Suite 14, Level 3<br>22 Harbourline Road,<br>Riverton NSW 2199</p>
    <p class="contact-line">+61 2 9000 4812
      <svg class="contact-icon" viewBox="0 0 10 10"><circle cx="5" cy="5" r="5" fill="var(--mid-blue)"/><path d="M3.2 2.6l1 1-0.6 0.7c0.4 0.8 1 1.4 1.8 1.8l0.7-0.6 1 1-0.7 0.8C4.8 7.2 2.8 5.2 2.4 3.3z" fill="#fff"/></svg></p>
    <p class="contact-line">www.mrtproperty.com.au
      <svg class="contact-icon" viewBox="0 0 10 10"><circle cx="5" cy="5" r="5" fill="var(--mid-blue)"/><circle cx="5" cy="5" r="3" fill="none" stroke="#fff" stroke-width="0.7"/><path d="M2 5h6M5 2v6" stroke="#fff" stroke-width="0.6"/></svg></p>
    <p class="contact-line">hello@mrtproperty.com.au
      <svg class="contact-icon" viewBox="0 0 10 10"><circle cx="5" cy="5" r="5" fill="var(--mid-blue)"/><rect x="2.4" y="3.2" width="5.2" height="3.6" fill="none" stroke="#fff" stroke-width="0.6"/><path d="M2.4 3.2L5 5.3 7.6 3.2" fill="none" stroke="#fff" stroke-width="0.6"/></svg></p>
  </div>
  <svg class="bottom-wave" viewBox="0 0 438 170" preserveAspectRatio="none">
    <path d="M0 0 C40 90 170 150 438 162 L438 170 L0 170 Z" fill="var(--sky)"/>
    <path d="M0 4 C36 92 164 148 438 158" fill="none" stroke="var(--paper)" stroke-width="3"/>
    <path d="M0 10 C30 100 150 152 438 166 L438 170 L0 170 Z" fill="var(--deep-blue)"/>
  </svg>
</section>

<section class="sheet compliment-slip" aria-label="Compliment slip">
  <div class="brand-name"><span class="brand-dot"></span>MRT Property</div>
  <div class="contact">
    <p class="address">Suite 14, Level 3<br>22 Harbourline Road,<br>Riverton NSW 2199</p>
    <p class="contact-line">+61 2 9000 4812
      <svg class="contact-icon" viewBox="0 0 10 10"><circle cx="5" cy="5" r="5" fill="var(--mid-blue)"/><path d="M3.2 2.6l1 1-0.6 0.7c0.4 0.8 1 1.4 1.8 1.8l0.7-0.6 1 1-0.7 0.8C4.8 7.2 2.8 5.2 2.4 3.3z" fill="#fff"/></svg></p>
    <p class="contact-line">www.mrtproperty.com.au
      <svg class="contact-icon" viewBox="0 0 10 10"><circle cx="5" cy="5" r="5" fill="var(--mid-blue)"/><circle cx="5" cy="5" r="3" fill="none" stroke="#fff" stroke-width="0.7"/><path d="M2 5h6M5 2v6" stroke="#fff" stroke-width="0.6"/></svg></p>
    <p class="contact-line">hello@mrtproperty.com.au
      <svg class="contact-icon" viewBox="0 0 10 10"><circle cx="5" cy="5" r="5" fill="var(--mid-blue)"/><rect x="2.4" y="3.2" width="5.2" height="3.6" fill="none" stroke="#fff" stroke-width="0.6"/><path d="M2.4 3.2L5 5.3 7.6 3.2" fill="none" stroke="#fff" stroke-width="0.6"/></svg></p>
  </div>
  <svg class="bottom-wave" viewBox="0 0 580 110" preserveAspectRatio="none">
    <path d="M0 0 C60 60 240 98 580 104 L580 110 L0 110 Z" fill="var(--sky)"/>
    <path d="M0 3 C56 62 230 96 580 101" fill="none" stroke="var(--slip-paper)" stroke-width="2.5"/>
    <path d="M0 8 C50 70 220 100 580 108 L580 110 L0 110 Z" fill="var(--deep-blue)"/>
  </svg>
</section>

<section class="sheet envelope" aria-label="Envelope back">
  <svg class="envelope-flap" viewBox="0 0 580 290" preserveAspectRatio="none">
    <path d="M0 290 L250 150 M580 290 L330 150" stroke="var(--envelope-edge)" stroke-width="1.5" fill="none"/>
    <path d="M0 0 L580 0 L580 110 Q570 128 548 128 L32 128 Q10 128 0 110 Z" fill="var(--envelope)" stroke="var(--envelope-edge)" stroke-width="1.5"/>
  </svg>
</section>

</body>
</html>
```